Exciting Graphics for Print Booth Display Car theme

We are a Business Intelligence company that provides business performance solutions to small and large companies. We need new graphics designed for our 10' conference booth that will be printed . We would like to use images that promote high performance and use the image of a moving sports car (Vantrell) across a road or with some movement in background.
- Our theme for these graphics include "Geared up for the Road Ahead...No Limits". Could use a black background or maybe include a road, or track or movement and/or racing references or reference to "super" cars, and high performance cars.
- Our branding includes our logo that includes blues of PMS 293 and Process Blue.
- Our company tagline is Listen. Collaborate. Solve. We would like to incorporate this into the design.
- The other colors that could be incorporated are red, orange, blue, yellow.
- We also need to include the Quintara partner logo.
- Our prominent services are Quintara Consulting, Education, Support. We would like this to be included in the design also.
There are 4 panels that will come together to make a 10' foot booth with overall dimension of 89 1/2" by 110 1/2" and we need high res 300 dpi or greater images. The images provided are examples of what we would like included, but have not been purchased. We want to have the Vantrell KX7 car used in the design.
Reason: We would like to extend the deadline to allow for additional submissions.
thank you
Target Market(s)
Business intelligence decision makers
Industry/Entity Type
Racing
Requirements
Must have
- - Must have graphics: Company logo, Quintara Partner logo without the word gold- just Quintara Partner, Tagline- Listen. Collaborate. Solve.
- Consider logo and word placement in final design: Logo and wording should be primarily on the top half of artwork - since this is a booth graphic, the lower half of the display may be blocked by tables and people.
Nice to have
- high contrast, vibrant

```html
<!DOCTYPE html>
<html lang="en">
<head>
<meta charset="utf-8">
<title>KDL Booth Graphic – Geared Up for the Road Ahead</title>
<link rel="stylesheet" href="https://fonts.googleapis.com/css2?family=Anton&family=Raleway:wght@300;700&family=Saira+Condensed:ital,wght@1,700&display=swap">
<style>
  :root {
    --stage: #1c1c1c;
    --divider: #262626;
    --brand-blue: #1f52b9;
    --brand-blue-light: #3a7be0;
    --process-blue: #1fa3e0;
    --navy: #12245e;
    --race-red: #e23a1e;
    --race-orange: #f2772a;
    --white: #ffffff;
    --partner-red: #d9262c;
    --headline-dark: #0c3597;
    --headline-light: #2166d6;
  }
  html, body {
    margin: 0;
    width: 1200px;
    height: 892px;
    overflow: hidden;
    background: var(--stage);
  }
  .booth { display: block; width: 1200px; height: 892px; }
  .tagline {
    font-family: "Raleway", sans-serif;
    font-weight: 300;
    font-size: 20px;
    letter-spacing: 2px;
    fill: var(--white);
  }
  .brand-name {
    font-family: "Raleway", sans-serif;
    font-weight: 700;
    font-size: 58px;
    fill: var(--navy);
  }
  .services {
    font-family: "Saira Condensed", sans-serif;
    font-style: italic;
    font-weight: 700;
    font-size: 38px;
    fill: var(--white);
    letter-spacing: 1px;
  }
  .services .dot { fill: var(--process-blue); }
  .headline {
    font-family: "Anton", sans-serif;
    font-size: 70px;
    fill: url(#headlineFill);
  }
</style>
</head>
<body>
<svg class="booth" viewBox="0 0 1200 892" xmlns="http://www.w3.org/2000/svg">
  <defs>
    <linearGradient id="skyBlue" x1="0" y1="1" x2="1" y2="0">
      <stop offset="0" stop-color="var(--brand-blue)"/>
      <stop offset="1" stop-color="var(--brand-blue-light)"/>
    </linearGradient>
    <linearGradient id="halftoneBand" x1="0" y1="0" x2="0.6" y2="1">
      <stop offset="0" stop-color="var(--race-orange)" stop-opacity="0.55"/>
      <stop offset="1" stop-color="#fbe2d2" stop-opacity="0"/>
    </linearGradient>
    <linearGradient id="trackScene" x1="0" y1="0" x2="0" y2="1">
      <stop offset="0" stop-color="#f4f5f6"/>
      <stop offset="0.5" stop-color="#c9cecb"/>
      <stop offset="0.7" stop-color="#6b726e"/>
      <stop offset="1" stop-color="#2e3034"/>
    </linearGradient>
    <linearGradient id="headlineFill" x1="0" y1="0" x2="1" y2="0">
      <stop offset="0" stop-color="var(--headline-dark)"/>
      <stop offset="1" stop-color="var(--headline-light)"/>
    </linearGradient>
  </defs>

  <!-- lower photo area, running behind the whole banner -->
  <g class="track-photo" role="img" aria-label="Blue Vantrell KX7 sports car speeding along a race track with motion-blurred barriers behind">
    <rect x="111" y="48" width="969" height="776" fill="url(#trackScene)"/>
  </g>

  <!-- orange speed band -->
  <path class="speed-band" d="M111 405 C420 380 800 320 1080 262 L1080 360 C800 420 420 470 111 500 Z" fill="url(#halftoneBand)"/>

  <!-- blue sky field with red edge -->
  <path class="edge-stripe" d="M111 48 H1080 V272 C800 330 420 392 111 415 Z" fill="var(--race-red)"/>
  <path class="sky-field" d="M111 48 H1080 V262 C800 320 420 382 111 405 Z" fill="url(#skyBlue)"/>

  <!-- white logo tab -->
  <path class="logo-tab" d="M364 48 H826 V212 Q826 248 790 248 H400 Q364 248 364 212 Z" fill="var(--white)"/>
  <rect class="brand-square" x="404" y="150" width="40" height="40" fill="var(--process-blue)"/>
  <text class="brand-name" x="456" y="192">KDL</text>
  <rect class="partner-badge" x="618" y="138" width="168" height="54" rx="6" fill="var(--partner-red)"/>

  <text class="tagline" x="597" y="280" text-anchor="middle">LISTEN.&#160;&#160;COLLABORATE.&#160;&#160;SOLVE.</text>

  <text class="services" transform="translate(588 350) rotate(-6.3) skewX(-6)" text-anchor="middle" textLength="670" lengthAdjust="spacingAndGlyphs">CONSULTING <tspan class="dot">•</tspan> EDUCATION SUPPORT <tspan class="dot">•</tspan> STAFFING</text>

  <text class="headline" transform="translate(592 488) rotate(-8) skewX(-12)" text-anchor="middle" textLength="840" lengthAdjust="spacingAndGlyphs">GEARED UP FOR THE ROAD AHEAD</text>

  <!-- panel seams -->
  <g class="panel-seams" fill="var(--divider)">
    <rect x="350" y="48" width="4" height="776"/>
    <rect x="593" y="48" width="4" height="776"/>
    <rect x="836" y="48" width="4" height="776"/>
  </g>
</svg>
</body>
</html>
```